Quorva - corporate Business Card

We need a good look and innovative business card for a new start up company based in Los Angeles called "Quorva". We are in a payment business, including payment card, app, and ewallet. We are expert in online payment and Card not present (CNP) transaction.
We need an innovative, modern business card.

Our logo font is Aero Matics

Target Market(s)

Startup - Bank - Online Payment - Card Manufacturing

Industry/Entity Type

Startup

Contact Information for Business Card

phone: 555 014 7396 - Address: 4172 Marlowe blvd, Brennick Falls, NV 90299

Requirements
Must have
• Message: innovative, professional, expert, high tech, trust, online payment expert, security
Nice to have
• no comment
Should not have
• no Comment

```html
<!DOCTYPE html>
<html lang="en">
<head>
<meta charset="utf-8">
<title>Quorva – Business Card</title>
<link rel="stylesheet" href="https://fonts.googleapis.com/css2?family=Arimo:wght@400;700&display=swap">
<style>
  :root {
    --stage: #2b2b2d;
    --card-white: #ffffff;
    --card-mist: #ececec;
    --brand-red: #a51d2d;
    --brand-red-dark: #8a1624;
    --slate: #3a3a3c;
    --ink: #222222;
    --soft-text: #e6e6e6;
    --ring: #dcdcdc;
  }
  * { box-sizing: border-box; margin: 0; padding: 0; }
  html, body {
    width: 1200px; height: 997px; overflow: hidden;
    background: var(--stage);
    font-family: "Arimo", Arial, sans-serif;
  }
  .stage {
    position: relative; width: 1200px; height: 997px;
    display: flex; align-items: center; justify-content: center; gap: 50px;
  }
  .card {
    position: relative; width: 520px; height: 297px;
    border-radius: 6px; overflow: hidden;
    box-shadow: 0 12px 30px rgba(0,0,0,.45);
  }

  /* Front */
  .card--front {
    background: linear-gradient(160deg, var(--card-white) 0%, var(--card-mist) 100%);
    display: flex; align-items: center; justify-content: center; gap: 14px;
  }
  .brand-dot {
    width: 78px; height: 78px; border-radius: 50%;
    background: var(--brand-red);
  }
  .brand-name {
    font-weight: 700; color: var(--brand-red);
    font-size: 58px; letter-spacing: 1px; line-height: 1;
  }

  /* Back */
  .card--back { background: var(--card-white); }
  .card__art { position: absolute; inset: 0; }
  .back-brand {
    position: absolute; top: 24px; right: 30px;
    font-weight: 700; color: var(--brand-red);
    font-size: 32px; letter-spacing: 1px;
  }
  .holder { position: absolute; top: 92px; left: 34px; }
  .holder__name { font-weight: 700; font-size: 19px; color: var(--brand-red); }
  .holder__role { font-size: 12px; color: var(--ink); margin-top: 3px; }

  .contacts {
    position: absolute; left: 42px; top: 198px;
    list-style: none; color: var(--soft-text); font-size: 12.5px;
  }
  .contacts li { display: flex; align-items: flex-start; gap: 9px; line-height: 17px; }
  .contacts .icon {
    flex: none; width: 12px; height: 12px; margin-top: 2px;
    border-radius: 2px; background: var(--brand-red);
    display: flex; align-items: center; justify-content: center;
  }
</style>
</head>
<body>
<main class="stage">

  <section class="card card--front" aria-label="Card front">
    <span class="brand-dot"></span>
    <span class="brand-name">quorva</span>
  </section>

  <section class="card card--back" aria-label="Card back">
    <svg class="card__art" viewBox="0 0 520 297" aria-hidden="true">
      <path d="M0,182 C120,132 250,128 360,136 C430,141 480,128 520,120 L520,140 C480,148 430,158 360,156 C250,152 120,160 0,210 Z" fill="var(--brand-red)"/>
      <path d="M0,210 C120,160 250,152 360,156 C430,158 480,148 520,140 L520,297 L0,297 Z" fill="var(--slate)"/>
      <circle cx="425" cy="132" r="44" fill="var(--brand-red-dark)" stroke="var(--ring)" stroke-width="6"/>
    </svg>

    <div class="back-brand">quorva</div>

    <div class="holder">
      <div class="holder__name">Dana Whitlock</div>
      <div class="holder__role">Director</div>
    </div>

    <ul class="contacts">
      <li>
        <span class="icon"><svg width="8" height="8" viewBox="0 0 8 8"><rect x="2" y="0.5" width="4" height="7" rx="1" fill="none" stroke="#fff" stroke-width="1"/></svg></span>
        07700 900318
      </li>
      <li>
        <span class="icon"><svg width="8" height="8" viewBox="0 0 8 8"><path d="M1,3 Q4,0 7,3 L6,4 L5,3 L3,3 L2,4 Z M2,5 H6 V7 H2 Z" fill="#fff"/></svg></span>
        555 014 7396
      </li>
      <li>
        <span class="icon"><svg width="8" height="8" viewBox="0 0 8 8"><rect x="0.5" y="1.5" width="7" height="5" fill="none" stroke="#fff" stroke-width="1"/><path d="M0.5,1.5 L4,4.5 L7.5,1.5" fill="none" stroke="#fff" stroke-width="1"/></svg></span>
        dana@quorva.com
      </li>
      <li>
        <span class="icon"><svg width="8" height="8" viewBox="0 0 8 8"><path d="M4,0.5 L7.5,3.5 H6.5 V7.5 H1.5 V3.5 H0.5 Z" fill="#fff"/></svg></span>
        <span>4172 Marlowe blvd, Brennick Falls,<br>NV 90299</span>
      </li>
    </ul>
  </section>

</main>
</body>
</html>
```